Wine label for family vineyard start-up

Brand new family vineyard needs a new label:

The information we need on the label is the following:
- Merlot & Cabernet (variety)
- Colle Varenzo (location)
- 2016 (vintage)

The style of the label should be graphic / minimal / masculine.

This is a wine made by three 35yr old guys

Target Market(s)

young & urban

Industry/Entity Type

Vineyard

Logo Text

Merlot & Cabernet / Colle Varenzo / 2016

Font styles to use
Sans Serif

Requirements
Must have
• clearly legible
• aesthetically pleasing [minimalist]
• sans serif

```html
<!DOCTYPE html>
<html lang="en">
<head>
<meta charset="UTF-8">
<title>Colle Varenzo — Merlot &amp; Cabernet 2016</title>
<link rel="stylesheet" href="https://fonts.googleapis.com/css2?family=Plus+Jakarta+Sans:wght@300;700;800&display=swap">
<style>
  :root {
    --backdrop: #2a2a2a;
    --label-red: #a7092f;
    --label-red-deep: #7d0522;
    --label-red-right: #8f0629;
    --cream: #f1e3c3;
    --variety-tone: #d9919c;
  }

  html, body {
    margin: 0;
    padding: 0;
    width: 716px;
    height: 1200px;
    overflow: hidden;
    background: var(--backdrop);
  }

  .canvas {
    position: relative;
    width: 716px;
    height: 1200px;
  }

  .wine-label {
    position: absolute;
    left: 58px;
    top: 261px;
    width: 600px;
    height: 678px;
    background: linear-gradient(90deg,
      var(--label-red) 0%,
      var(--label-red) 38%,
      var(--label-red-deep) 52%,
      var(--label-red-right) 78%,
      var(--label-red-right) 100%);
    font-family: "Plus Jakarta Sans", sans-serif;
    color: var(--cream);
  }

  .estate-name {
    position: absolute;
    left: 24px;
    top: 30px;
    margin: 0;
    font-weight: 800;
    font-size: 89px;
    line-height: 93px;
    letter-spacing: -1px;
  }

  .estate-name span { display: block; }

  .vintage {
    position: absolute;
    left: 196px;
    top: 270px;
    margin: 0;
    writing-mode: vertical-rl;
    transform: rotate(180deg);
    font-weight: 700;
    font-size: 17px;
    letter-spacing: 4px;
  }

  .variety {
    position: absolute;
    left: 450px;
    top: 430px;
    margin: 0;
    writing-mode: vertical-rl;
    transform: rotate(180deg);
    font-weight: 300;
    font-size: 31px;
    line-height: 34px;
    color: var(--variety-tone);
  }
</style>
</head>
<body>
  <main class="canvas">
    <section class="wine-label">
      <h1 class="estate-name">
        <span>Colle</span>
        <span>Varenzo</span>
      </h1>
      <p class="vintage">2016</p>
      <p class="variety">Merlot &amp;<br>Cabernet</p>
    </section>
  </main>
</body>
</html>
```